Website Design - TallyPorchHelpers.net

PLEASE CHECK WORD DOCUMENT ATTACHED FOR WEBSITE FLOW.

Target Market(s)

REAL ESTATE AGENTS ARE THE TARGET MARKET

Industry/Entity Type

Real Estate

Coding

Coded - Design and coding required

Number of Pages Required

4 page

Colors

Designer to choose colors to be used in the design.

Requirements
Must have
• WE LIKE RED LOGO ATTACHED
Nice to have
• PLEASE CHECK WORD DOCUMENT ATTACHED FOR WEBSITE FLOW.
Should not have

```html
<!DOCTYPE html>
<html lang="en">
<head>
<meta charset="utf-8">
<title>Tally Porch Helpers</title>
<link href="https://fonts.googleapis.com/css2?family=Roboto:wght@400;500;700;900&family=Oswald:wght@500;600&display=swap" rel="stylesheet">
<style>
:root{
  --red:#d0141e;
  --red-dark:#a80f17;
  --navy:#22207a;
  --navy-deep:#1a1860;
  --ink:#1e1e22;
  --grey-text:#555;
  --light:#f1f1f1;
  --footer:#1c1c20;
  --white:#fff;
}
*{box-sizing:border-box;margin:0;padding:0}
html,body{width:1200px;height:5310px;overflow:hidden}
body{position:relative;font-family:"Roboto",Arial,sans-serif;color:var(--ink);background:var(--white)}
.abs{position:absolute}
.center{text-align:center}
.h-section{font-weight:700;font-size:32px;letter-spacing:1px;text-transform:uppercase;text-align:center;line-height:1.35}

/* header */
.site-header{left:0;top:0;width:1200px;height:124px;background:var(--white)}
.brand{left:130px;top:14px;display:flex;align-items:center;gap:12px}
.brand-box{width:34px;height:34px;background:var(--red)}
.brand-name{font-family:"Oswald",sans-serif;font-weight:600;font-size:26px;color:var(--red);line-height:1;text-transform:uppercase;width:160px}
.topbar{left:480px;top:0;width:720px;height:32px;background:var(--red);color:var(--white);font-size:13px;display:flex;align-items:center;padding-left:70px;gap:20px}
.topbar .search{width:170px;height:20px;background:var(--white);border-radius:10px;color:#999;font-size:10px;padding:3px 10px;margin-left:auto;margin-right:50px}
.nav{left:560px;top:66px;display:flex;gap:38px;font-size:14px;font-weight:500;text-transform:uppercase}

/* hero */
.hero{left:0;top:124px;width:1200px;height:680px;overflow:hidden}
.hero-photo{position:absolute;inset:0;background:linear-gradient(180deg,#8b9cae 0%,#a8b3bb 35%,#6a7356 62%,#3f5a2c 100%)}
.hero-msg{left:322px;top:255px;width:625px;height:160px;background:rgba(20,20,30,.72);border:2px solid var(--white);color:var(--white);font-family:"Oswald",sans-serif;font-weight:500;font-size:24px;line-height:1.45;text-transform:uppercase;padding:26px 24px;text-align:center}
.hero-curve{left:0;bottom:0}
.dots{display:flex;gap:6px}
.dot{width:11px;height:11px;border-radius:50%;border:2px solid var(--navy);background:var(--white)}
.dot.on{background:var(--navy)}

/* choose */
.choose-title{left:0;top:858px;width:1200px}
.choose-title .accent{display:inline-block;border-bottom:3px solid var(--red)}
.choose-btns{left:0;top:975px;width:1200px;display:flex;justify-content:center;gap:18px}
.pill{height:36px;border-radius:18px;border:2px solid var(--navy);color:var(--navy);font-size:15px;font-weight:500;padding:0 22px;display:flex;align-items:center;text-transform:uppercase}
.pill.active{background:var(--red);border-color:var(--red);color:var(--white)}

/* how it works */
.how-title{left:0;top:1085px;width:1200px;font-size:38px}
.how-sub{left:0;top:1137px;width:1200px;font-size:15px;letter-spacing:3px;color:var(--grey-text)}
.step{width:260px;text-align:center}
.step-badge{width:120px;height:120px;margin:0 auto;border-radius:50%;border:3px solid var(--red);display:flex;align-items:center;justify-content:center;font-family:"Oswald",sans-serif;font-size:68px;color:var(--red)}
.step p{margin-top:30px;font-size:13px;line-height:1.6;color:var(--grey-text)}
.step-arrow{top:1265px}

/* pricing */
.pricing{left:0;top:1540px;width:1200px;height:655px;background:var(--navy)}
.pricing-title{left:0;top:1595px;width:1200px;color:var(--white);font-size:40px}
.plans{left:10px;top:1682px;width:1180px;display:flex;gap:12px}
.plan{width:227px;height:500px;background:var(--white);position:relative}
.plan-top{height:125px;background:var(--navy-deep);display:flex;align-items:center;justify-content:center;border:4px solid var(--white);border-bottom:none}
.plan-badge{width:88px;height:88px;border-radius:50%;background:var(--navy);border:3px solid var(--white);color:var(--white);display:flex;flex-direction:column;align-items:center;justify-content:center;font-weight:700;line-height:1}
.plan-badge b{font-size:30px}
.plan-badge span{font-size:13px;margin-top:3px}
.plan-price{height:42px;background:var(--red);color:var(--white);font-size:26px;font-weight:700;display:flex;align-items:center;justify-content:center}
.plan-price.small{font-size:11px}
.plan ul{list-style:none;padding:18px 14px 0 14px}
.plan li{position:relative;padding-left:22px;font-size:12px;line-height:1.55;color:var(--grey-text);margin-bottom:12px}
.plan li svg{position:absolute;left:0;top:3px}
.buy{position:absolute;left:14px;top:362px;height:30px;padding:0 16px;background:var(--navy);color:var(--white);font-size:12px;font-weight:700;border-radius:4px;display:flex;align-items:center}
.plan-note{position:absolute;left:14px;top:408px;right:12px;color:var(--navy);font-size:12px;line-height:1.5;font-weight:500}

/* subscription */
.sub-title{left:0;top:2280px;width:1200px;font-size:30px}
.service{width:220px;text-align:center}
.service-icon{width:92px;height:92px;border-radius:50%;background:var(--red);margin:0 auto;display:flex;align-items:center;justify-content:center}
.service h3{font-size:20px;font-weight:700;margin:24px 0 14px}
.service p{font-size:13px;line-height:1.6;color:var(--grey-text)}

/* map */
.map{left:0;top:2850px;width:1200px;height:530px;background:linear-gradient(135deg,#e9e3d4 0%,#d9d6c2 45%,#a9c6da 70%,#8fb4cf 100%)}
.area-card{left:250px;top:2800px;width:700px;height:150px;background:var(--white);box-shadow:0 4px 14px rgba(0,0,0,.25);text-align:center;padding-top:22px}
.area-card h2{font-size:32px;font-weight:700;text-transform:uppercase;letter-spacing:1px}
.area-input{position:absolute;left:35px;top:85px;width:570px;height:40px;border:1px solid #ccc;font-size:11px;color:#999;text-align:left;padding:12px 16px}
.area-go{position:absolute;left:620px;top:83px;width:44px;height:44px;border-radius:50%;background:var(--red);display:flex;align-items:center;justify-content:center}

/* faq */
.faq-title{left:0;top:3485px;width:1200px;font-size:36px}
.faq{left:275px;top:3565px;width:655px}
.faq-open{background:var(--red);color:var(--white);height:36px;font-size:13px;font-weight:500;display:flex;align-items:center;justify-content:space-between;padding:0 12px}
.faq-body{border:1px solid #ddd;border-top:none;font-size:12.5px;line-height:1.6;color:var(--grey-text);padding:14px 18px;height:92px}
.faq-item{margin-top:10px;height:32px;border:1px solid #ddd;font-size:13px;display:flex;align-items:center;justify-content:space-between;padding-left:12px;color:#444}
.faq-toggle{width:32px;height:32px;background:var(--red);display:flex;align-items:center;justify-content:center}

/* testimonials */
.testi{left:0;top:4010px;width:1200px;height:450px;background:linear-gradient(180deg,#b3141c 0%,#9e1017 100%)}
.testi-title{left:0;top:4095px;width:1200px;color:var(--white);font-size:30px}
.quote{width:300px;display:flex;gap:16px;color:var(--white)}
.avatar{width:62px;height:62px;flex:none;border-radius:50%;background:#d9c7be;border:3px solid var(--white)}
.quote p{font-size:12px;line-height:1.55}
.quote .who{margin-top:8px;font-size:12px;font-weight:700}
.quote .who span{display:block;font-weight:400}
.testi-dots .dot{border-color:var(--white);background:transparent}
.testi-dots .dot.on{background:var(--white)}

/* footer */
.footer{left:0;top:4710px;width:1200px;height:600px;background:var(--footer);color:var(--white)}
.contact-card{left:130px;top:4495px;width:940px;height:340px;background:var(--light)}
.contact-card h2{text-align:center;color:var(--navy);font-size:32px;font-weight:700;text-transform:uppercase;margin-top:26px}
.field{position:absolute;height:34px;background:var(--white);border:1px solid #ccc;font-size:11px;color:#888;padding:10px 12px}
.submit{position:absolute;left:360px;top:268px;width:220px;height:40px;background:var(--navy);color:var(--white);font-weight:700;font-size:15px;display:flex;align-items:center;justify-content:center}
.f-col h3{font-size:19px;font-weight:700;text-transform:uppercase;line-height:1.3;margin-bottom:16px}
.f-col p{font-size:12px;line-height:1.65;color:#ddd}
.f-line{display:flex;gap:10px;font-size:12px;color:#ddd;margin-bottom:12px;line-height:1.4}
.f-links{list-style:none;font-size:12px;color:#ddd;line-height:1.9}
.f-links li::before{content:"› ";}
.f-brand{display:flex;align-items:center;gap:10px}
.f-brand .brand-box{background:var(--white)}
.f-brand .brand-name{color:var(--white);font-size:22px;width:140px}
.socials{display:flex;gap:6px;margin-top:16px;margin-left:20px}
.socials span{width:26px;height:26px;border-radius:50%;border:1.5px solid var(--white)}
.copy{left:0;top:5225px;width:1200px;text-align:center;font-size:11px;color:#ccc;line-height:2.4}
</style>
</head>
<body>

<header class="site-header abs">
  <div class="brand abs"><div class="brand-box"></div><div class="brand-name">Tally Porch Helpers</div></div>
  <div class="topbar abs">
    <svg width="14" height="14" viewBox="0 0 24 24" fill="#fff"><path d="M6.6 10.8c1.4 2.8 3.8 5.1 6.6 6.6l2.2-2.2c.3-.3.7-.4 1-.2 1.1.4 2.3.6 3.6.6.6 0 1 .4 1 1V20c0 .6-.4 1-1 1C10.6 21 3 13.4 3 4c0-.6.4-1 1-1h3.5c.6 0 1 .4 1 1 0 1.3.2 2.5.6 3.6.1.3 0 .7-.2 1z"/></svg>
    <span>Call Or Text Us 1-555-014-0199</span>
    <div class="search">Enter your search keyword</div>
  </div>
  <nav class="nav abs"><span>How It Works</span><span>Service Area</span><span>Pricing</span><span>About Us</span><span>FAQ</span></nav>
</header>

<section class="hero abs">
  <div class="hero-photo" role="img" aria-label="Photo of a two-storey suburban house with a front garden and an open house sign on the lawn"></div>
  <div class="hero-msg abs">Helping agents save time and money. We place signs and boost foot traffic to your open houses using proven marketing techniques.</div>
  <svg class="hero-curve abs" width="1200" height="120" viewBox="0 0 1200 120" preserveAspectRatio="none">
    <path d="M0 20 Q600 150 1200 20 L1200 120 L0 120 Z" fill="#22207a"/>
    <path d="M0 60 Q600 170 1200 60 L1200 120 L0 120 Z" fill="#fff"/>
  </svg>
  <div class="dots abs" style="left:573px;top:632px"><span class="dot on"></span><span class="dot"></span><span class="dot"></span></div>
</section>

<h2 class="choose-title h-section abs">Choose the option below that<br><span class="accent">best describes you</span></h2>
<div class="choose-btns abs">
  <span class="pill">I'm a full on brokerage</span>
  <span class="pill active">I'm an ind. broker with a team</span>
  <span class="pill">I need sign placement ASAP</span>
</div>

<h2 class="how-title h-section abs">How it works?</h2>
<p class="how-sub abs center">3 Easy Steps</p>
<div class="step abs" style="left:140px;top:1205px"><div class="step-badge">1</div><p>We boost foot traffic to your open houses using proven marketing channels, social ads, text notifications, voice broadcasts and email notifications</p></div>
<div class="step abs" style="left:470px;top:1205px"><div class="step-badge">2</div><p>We place open house signs strategically in the surrounding area</p></div>
<div class="step abs" style="left:800px;top:1205px"><div class="step-badge">3</div><p>We pick up the signs once your open house ends</p></div>
<svg class="step-arrow abs" style="left:370px" width="110" height="20"><path d="M2 10 H100 M92 4 L100 10 L92 16" stroke="#22207a" stroke-width="2" fill="none"/></svg>
<svg class="step-arrow abs" style="left:700px" width="110" height="20"><path d="M2 10 H100 M92 4 L100 10 L92 16" stroke="#22207a" stroke-width="2" fill="none"/></svg>

<section class="pricing abs"></section>
<h2 class="pricing-title h-section abs">Pricing</h2>
<div class="plans abs">
  <div class="plan"><div class="plan-top"><div class="plan-badge"><b>5</b><span>SIGNS</span></div></div><div class="plan-price">$49</div>
    <ul><li><svg width="12" height="12"><path d="M1 6 L5 10 L11 2" stroke="#d0141e" stroke-width="2" fill="none"/></svg>Place signs strategically in best areas according to where the open house is located</li><li><svg width="12" height="12"><path d="M1 6 L5 10 L11 2" stroke="#d0141e" stroke-width="2" fill="none"/></svg>Pick up the signs after the open house</li><li><svg width="12" height="12"><path d="M1 6 L5 10 L11 2" stroke="#d0141e" stroke-width="2" fill="none"/></svg>Store custom signs for you if needed</li></ul>
    <span class="buy">BUY NOW</span><p class="plan-note">Sign Up For A Subscription To Receive Our Marketing Components For FREE.</p></div>
  <div class="plan"><div class="plan-top"><div class="plan-badge"><b>10</b><span>SIGNS</span></div></div><div class="plan-price">$59</div>
    <ul><li><svg width="12" height="12"><path d="M1 6 L5 10 L11 2" stroke="#d0141e" stroke-width="2" fill="none"/></svg>Place signs strategically in best areas according to where the open house is located</li><li><svg width="12" height="12"><path d="M1 6 L5 10 L11 2" stroke="#d0141e" stroke-width="2" fill="none"/></svg>Pick up the signs after the open house</li><li><svg width="12" height="12"><path d="M1 6 L5 10 L11 2" stroke="#d0141e" stroke-width="2" fill="none"/></svg>Store custom signs for you if needed</li></ul>
    <span class="buy">BUY NOW</span><p class="plan-note">Sign Up For A Subscription To Receive Our Marketing Components For FREE.</p></div>
  <div class="plan"><div class="plan-top"><div class="plan-badge"><b>15</b><span>SIGNS</span></div></div><div class="plan-price">$69</div>
    <ul><li><svg width="12" height="12"><path d="M1 6 L5 10 L11 2" stroke="#d0141e" stroke-width="2" fill="none"/></svg>Place signs strategically in best areas according to where the open house is located</li><li><svg width="12" height="12"><path d="M1 6 L5 10 L11 2" stroke="#d0141e" stroke-width="2" fill="none"/></svg>Pick up the signs after the open house</li><li><svg width="12" height="12"><path d="M1 6 L5 10 L11 2" stroke="#d0141e" stroke-width="2" fill="none"/></svg>Store custom signs for you if needed</li></ul>
    <span class="buy">BUY NOW</span><p class="plan-note">Sign Up For A Subscription To Receive Our Marketing Components For FREE.</p></div>
  <div class="plan"><div class="plan-top"><div class="plan-badge"><b>20</b><span>SIGNS</span></div></div><div class="plan-price">$79</div>
    <ul><li><svg width="12" height="12"><path d="M1 6 L5 10 L11 2" stroke="#d0141e" stroke-width="2" fill="none"/></svg>Place signs strategically in best areas according to where the open house is located</li><li><svg width="12" height="12"><path d="M1 6 L5 10 L11 2" stroke="#d0141e" stroke-width="2" fill="none"/></svg>Pick up the signs after the open house</li><li><svg width="12" height="12"><path d="M1 6 L5 10 L11 2" stroke="#d0141e" stroke-width="2" fill="none"/></svg>Store custom signs for you if needed</li></ul>
    <span class="buy">BUY NOW</span><p class="plan-note">Sign Up For A Subscription To Receive Our Marketing Components For FREE.</p></div>
  <div class="plan"><div class="plan-top"><div class="plan-badge"><b>25+</b><span>SIGNS</span></div></div><div class="plan-price small">CLICK BUY NOW TO CREATE CUSTOM PKG</div>
    <ul><li><svg width="12" height="12"><path d="M1 6 L5 10 L11 2" stroke="#d0141e" stroke-width="2" fill="none"/></svg>Place signs strategically in best areas according to where the open house is located</li><li><svg width="12" height="12"><path d="M1 6 L5 10 L11 2" stroke="#d0141e" stroke-width="2" fill="none"/></svg>Pick up the signs after the open house</li><li><svg width="12" height="12"><path d="M1 6 L5 10 L11 2" stroke="#d0141e" stroke-width="2" fill="none"/></svg>Store custom signs for you if needed</li></ul>
    <span class="buy">BUY NOW</span><p class="plan-note">Sign Up For A Subscription To Receive Our Marketing Components For FREE.</p></div>
</div>

<h2 class="sub-title h-section abs">Sign up for a subscription and get these<br>marketing services for free</h2>
<div class="service abs" style="left:120px;top:2435px"><div class="service-icon"><svg width="44" height="40" viewBox="0 0 44 40"><path d="M4 4 H40 V28 H18 L8 36 V28 H4 Z" fill="none" stroke="#fff" stroke-width="3"/><circle cx="14" cy="16" r="2.5" fill="#fff"/><circle cx="22" cy="16" r="2.5" fill="#fff"/><circle cx="30" cy="16" r="2.5" fill="#fff"/></svg></div><h3>SMS</h3><p>Send sms blast to your neighborhood informing them your home is for sale and if they know anyone looking to send them over</p></div>
<div class="service abs" style="left:370px;top:2435px"><div class="service-icon"><svg width="44" height="32" viewBox="0 0 44 32"><rect x="3" y="3" width="38" height="26" fill="none" stroke="#fff" stroke-width="3"/><path d="M3 3 L22 18 L41 3" fill="none" stroke="#fff" stroke-width="3"/></svg></div><h3>EMAIL</h3><p>Email blast to your neighborhood informing them your home is for sale and if they know anyone looking to send them over</p></div>
<div class="service abs" style="left:615px;top:2435px"><div class="service-icon"><svg width="42" height="38" viewBox="0 0 42 38"><path d="M4 14 H12 L30 4 V34 L12 24 H4 Z" fill="none" stroke="#fff" stroke-width="3" stroke-linejoin="round"/><path d="M35 13 Q39 19 35 25" fill="none" stroke="#fff" stroke-width="3"/></svg></div><h3>SOCIAL AD</h3><p>Newsfeed ads to people in your open house area</p></div>
<div class="service abs" style="left:860px;top:2435px"><div class="service-icon"><svg width="40" height="40" viewBox="0 0 40 40"><path d="M6 6 H22 L36 20 L20 36 L6 22 Z" fill="none" stroke="#fff" stroke-width="3"/><circle cx="14" cy="14" r="3" fill="#fff"/></svg></div><h3>VB</h3><p>VB blast to your neighborhood informing them your home is for sale and if they know anyone looking to send them over</p></div>

<section class="map abs" role="img" aria-label="Road map of the coastal service region"></section>
<div class="area-card abs">
  <h2>Service Area</h2>
  <div class="area-input">Enter your open house address to see if we service it</div>
  <div class="area-go"><svg width="18" height="18" viewBox="0 0 24 24"><path d="M2 11 L22 2 L13 22 L11 13 Z" fill="#fff"/></svg></div>
</div>

<h2 class="faq-title h-section abs">FAQs</h2>
<div class="faq abs">
  <div class="faq-open"><span>What is Lorem Ipsum?</span><svg width="16" height="16"><circle cx="8" cy="8" r="7" fill="#fff"/><path d="M4 8 H12" stroke="#d0141e" stroke-width="2"/></svg></div>
  <div class="faq-body">Sed ut perspiciatis unde omnis iste natus error sit voluptatem accusantium doloremque laudantium, totam rem aperiam, eaque ipsa quae ab illo inventore veritatis et quasi architecto beatae vitae dicta sunt explicabo. Nemo enim ipsam voluptatem quia voluptas.</div>
  <div class="faq-item"><span>Why do we use it?</span><span class="faq-toggle"><svg width="12" height="12"><path d="M2 6 H10 M6 2 V10" stroke="#fff" stroke-width="2"/></svg></span></div>
  <div class="faq-item"><span>Where can I get some?</span><span class="faq-toggle"><svg width="12" height="12"><path d="M2 6 H10 M6 2 V10" stroke="#fff" stroke-width="2"/></svg></span></div>
  <div class="faq-item"><span>Where does it come from?</span><span class="faq-toggle"><svg width="12" height="12"><path d="M2 6 H10 M6 2 V10" stroke="#fff" stroke-width="2"/></svg></span></div>
  <div class="faq-item"><span>What is Lorem Ipsum?</span><span class="faq-toggle"><svg width="12" height="12"><path d="M2 6 H10 M6 2 V10" stroke="#fff" stroke-width="2"/></svg></span></div>
</div>

<section class="testi abs" role="img" aria-label="Red tinted photo of a team meeting behind the testimonials"></section>
<h2 class="testi-title h-section abs">What our clients say</h2>
<div class="quote abs" style="left:130px;top:4195px"><div class="avatar"></div><div><p>“ At vero eos et accusamus et iusto odio dignissimos ducimus qui blanditiis praesentium voluptatum deleniti atque corrupti</p><p class="who">Marla Quinn<span>- tally porch helpers</span></p></div></div>
<div class="quote abs" style="left:450px;top:4195px"><div class="avatar"></div><div><p>“ At vero eos et accusamus et iusto odio dignissimos ducimus qui blanditiis praesentium voluptatum deleniti atque corrupti</p><p class="who">Marla Quinn<span>- tally porch helpers</span></p></div></div>
<div class="quote abs" style="left:780px;top:4195px"><div class="avatar"></div><div><p>“ At vero eos et accusamus et iusto odio dignissimos ducimus qui blanditiis praesentium voluptatum deleniti atque corrupti</p><p class="who">Marla Quinn<span>- tally porch helpers</span></p></div></div>
<div class="dots testi-dots abs" style="left:570px;top:4377px"><span class="dot on"></span><span class="dot"></span><span class="dot"></span><span class="dot"></span></div>

<footer class="footer abs">
  <div class="f-col abs" style="left:130px;top:200px;width:280px"><h3>About Tally<br>Porch Helpers</h3><p>Owned and operated by a highly experienced and skilled promoter, an expert marketer and a savvy realtor, we help agents leverage their time and skills to increase production at an affordable price with impeccable support.</p></div>
  <div class="f-col abs" style="left:490px;top:200px;width:220px"><h3>Contact Us</h3>
    <div class="f-line"><svg width="12" height="14" viewBox="0 0 12 16"><path d="M6 0 C2.7 0 0 2.7 0 6 C0 10 6 16 6 16 C6 16 12 10 12 6 C12 2.7 9.3 0 6 0 Z" fill="#fff"/><circle cx="6" cy="6" r="2.2" fill="#1c1c20"/></svg><span>Tally Porch Helpers<br>1420 Larkspur Row, Fenwick</span></div>
    <div class="f-line"><svg width="12" height="12" viewBox="0 0 24 24" fill="#fff"><path d="M6.6 10.8c1.4 2.8 3.8 5.1 6.6 6.6l2.2-2.2c.3-.3.7-.4 1-.2 1.1.4 2.3.6 3.6.6.6 0 1 .4 1 1V20c0 .6-.4 1-1 1C10.6 21 3 13.4 3 4c0-.6.4-1 1-1h3.5c.6 0 1 .4 1 1 0 1.3.2 2.5.6 3.6.1.3 0 .7-.2 1z"/></svg><span>Phone: 020 7946 0100</span></div>
    <div class="f-line"><svg width="12" height="10" viewBox="0 0 12 10"><rect x="0.5" y="0.5" width="11" height="9" fill="none" stroke="#fff"/><path d="M0.5 0.5 L6 5 L11.5 0.5" fill="none" stroke="#fff"/></svg><span>info@tallyporchhelpers.net</span></div>
    <div class="f-line"><svg width="12" height="12"><circle cx="6" cy="6" r="5" fill="none" stroke="#fff"/><path d="M6 3 V6 H8.5" stroke="#fff" fill="none"/></svg><span>Mon - Sun: 8:00 - 22:00</span></div>
  </div>
  <div class="f-col abs" style="left:738px;top:200px"><h3>Quick Links</h3><ul class="f-links"><li>How it Works</li><li>Service Area</li><li>Pricing</li><li>About Us</li><li>FAQ</li></ul></div>
  <div class="abs" style="left:905px;top:208px"><div class="f-brand"><div class="brand-box"></div><div class="brand-name">Tally Porch Helpers</div></div><div class="socials"><span></span><span></span><span></span><span></span></div></div>
</footer>
<div class="copy abs">© Copyright 2018 Tally Porch Helpers. All Rights Reserved.<br>Terms and Conditions | Privacy Policy</div>

<div class="contact-card abs">
  <h2>Contact us right now!</h2>
  <div class="field" style="left:80px;top:100px;width:380px">Name</div>
  <div class="field" style="left:80px;top:145px;width:380px">Email</div>
  <div class="field" style="left:80px;top:190px;width:380px">Cell Phone</div>
  <div class="field" style="left:480px;top:100px;width:380px;height:124px">Message</div>
  <div class="submit">SUBMIT</div>
</div>

</body>
</html>
```